Business Card For Halvenmoor Financial Consulting

Hi, I would like a business card designed. Bold, modern.
Please use the same design as the logo. I have also attached the website design to see the overall theme.
Wordmark Font
Color: Hex: #01AEF7

```html
<!DOCTYPE html>
<html lang="en">
<head>
<meta charset="utf-8">
<title>Halvenmoor Financial Consulting – Business Card</title>
<link rel="stylesheet" href="https://fonts.googleapis.com/css2?family=Open+Sans:wght@400;700&family=Montserrat:wght@300;400&display=swap">
<style>
  :root {
    --navy: #05436a;
    --sky: #3aa9e0;
    --white: #ffffff;
    --ink: #222222;
    --backdrop: #c9c9c9;
  }
  * { margin: 0; padding: 0; box-sizing: border-box; }
  html, body { width: 1200px; height: 896px; overflow: hidden; }
  body { background: var(--backdrop); position: relative; font-family: "Open Sans", sans-serif; }

  .card {
    position: absolute;
    left: 334px;
    width: 528px;
    height: 300px;
    overflow: hidden;
    box-shadow: 0 10px 18px rgba(0,0,0,0.25);
  }
  .card--front { top: 126px; background: var(--white); }
  .card--back { top: 475px; background: var(--navy); }

  .contact-band { position: absolute; inset: 0; width: 528px; height: 300px; }

  .brand-mark { position: absolute; background: var(--sky); }
  .brand-name {
    position: absolute;
    font-family: "Open Sans", sans-serif;
    font-weight: 700;
    text-transform: uppercase;
    line-height: 1;
  }
  .brand-name .line { display: block; }

  .card--front .brand-mark { left: 127px; top: 32px; width: 52px; height: 52px; }
  .card--front .brand-name { left: 0; width: 306px; top: 100px; text-align: center; color: var(--navy); }
  .card--front .brand-name .primary { font-size: 34px; letter-spacing: 2px; }
  .card--front .brand-name .secondary { font-size: 11px; letter-spacing: 4.5px; margin-top: 10px; }

  .person { position: absolute; right: 24px; top: 24px; text-align: right; }
  .person-name { font-size: 20px; font-weight: 700; color: var(--sky); line-height: 1.2; }
  .person-role { font-size: 14px; color: var(--ink); margin-top: 2px; }
  .address { position: absolute; right: 24px; top: 82px; text-align: right; font-size: 14px; line-height: 20px; color: var(--ink); font-style: normal; }

  .contacts {
    position: absolute; right: 24px; top: 192px;
    list-style: none; text-align: right;
    font-family: "Montserrat", sans-serif; font-weight: 300;
    font-size: 14px; line-height: 20px; color: var(--white);
  }
  .contacts li { display: flex; justify-content: flex-end; align-items: center; gap: 7px; }
  .contacts svg { width: 11px; height: 11px; fill: var(--sky); flex: none; }

  .card--back .brand-mark { left: 41px; top: 115px; width: 72px; height: 72px; }
  .card--back .brand-name { left: 130px; top: 113px; color: var(--white); }
  .card--back .brand-name .primary { font-size: 43px; letter-spacing: 2px; }
  .card--back .brand-name .secondary { font-size: 14px; letter-spacing: 6px; margin-top: 14px; }
</style>
</head>
<body>

<section class="card card--front" aria-label="Business card front">
  <svg class="contact-band" viewBox="0 0 528 300" aria-hidden="true">
    <path fill="var(--navy)" d="M0,272 C180,272 300,170 528,160 L528,300 L0,300 Z"/>
  </svg>

  <div class="brand-mark" aria-hidden="true"></div>
  <h1 class="brand-name">
    <span class="line primary">Halvenmoor</span>
    <span class="line secondary">Financial Consulting</span>
  </h1>

  <div class="person">
    <p class="person-name">MARCUS ELLERY</p>
    <p class="person-role">Managing Director</p>
  </div>
  <address class="address">
    Your address, City<br>State, Zip 1234
  </address>

  <ul class="contacts">
    <li>123 456 789
      <svg viewBox="0 0 24 24"><path d="M6.6 10.8a15.1 15.1 0 0 0 6.6 6.6l2.2-2.2a1 1 0 0 1 1-.25 11.4 11.4 0 0 0 3.6.57 1 1 0 0 1 1 1V20a1 1 0 0 1-1 1A17 17 0 0 1 3 4a1 1 0 0 1 1-1h3.5a1 1 0 0 1 1 1 11.4 11.4 0 0 0 .57 3.6 1 1 0 0 1-.25 1z"/></svg>
    </li>
    <li>123 456 789
      <svg viewBox="0 0 24 24"><path d="M7 1h10a2 2 0 0 1 2 2v18a2 2 0 0 1-2 2H7a2 2 0 0 1-2-2V3a2 2 0 0 1 2-2zm0 3v14h10V4zm5 15.5a1.2 1.2 0 1 0 0 2.4 1.2 1.2 0 0 0 0-2.4z"/></svg>
    </li>
    <li>info@halvenmoor.com
      <svg viewBox="0 0 24 24"><path d="M2 5h20v2l-10 6L2 7zm0 4.3 10 6 10-6V19H2z"/></svg>
    </li>
    <li>www.halvenmoor.com
      <svg viewBox="0 0 24 24"><path d="M12 2a10 10 0 1 0 0 20 10 10 0 0 0 0-20zm6.9 6h-3a15 15 0 0 0-1.3-3.9A8 8 0 0 1 18.9 8zM12 4c.9 1.2 1.6 2.6 2 4h-4c.4-1.4 1.1-2.8 2-4zM4.3 14a8 8 0 0 1 0-4h3.4a16 16 0 0 0 0 4zm.8 2h3a15 15 0 0 0 1.3 3.9A8 8 0 0 1 5.1 16zm3-8h-3a8 8 0 0 1 4.3-3.9A15 15 0 0 0 8.1 8zM12 20c-.9-1.2-1.6-2.6-2-4h4c-.4 1.4-1.1 2.8-2 4zm2.3-6H9.7a14 14 0 0 1 0-4h4.6a14 14 0 0 1 0 4zm.3 5.9A15 15 0 0 0 15.9 16h3a8 8 0 0 1-4.3 3.9zM16.3 14a16 16 0 0 0 0-4h3.4a8 8 0 0 1 0 4z"/></svg>
    </li>
  </ul>
</section>

<section class="card card--back" aria-label="Business card back">
  <div class="brand-mark" aria-hidden="true"></div>
  <p class="brand-name">
    <span class="line primary">Halvenmoor</span>
    <span class="line secondary">Financial Consulting</span>
  </p>
</section>

</body>
</html>
```